Business Cards for a law firm

Business cards for our law firm. Use our silhoette logo and OAK PARTNERS - check our website (www.oakpartners.example)

Contact Information for Business Card

our silhouette logo, OAK PARTNERS, 800-555-0147, Dorian Pemberton, dorian@oakpartners.example

Requirements
Must have
• our silhouette logo, OAK PARTNERS, 800-555-0147, Dorian Pemberton, dorian@oakpartners.example

```html
<!DOCTYPE html>
<html lang="en">
<head>
<meta charset="utf-8">
<title>Oak Partners — Business Cards</title>
<link rel="stylesheet" href="https://fonts.googleapis.com/css2?family=Montserrat:wght@300;400;700&display=swap">
<style>
  :root {
    --navy: #233470;
    --navy-soft: #3a4b88;
    --paper: #ffffff;
    --backdrop: #e6e7ea;
    --ink: #1c2340;
  }
  * { box-sizing: border-box; margin: 0; padding: 0; }
  html, body {
    width: 1200px; height: 900px; overflow: hidden;
    background: var(--backdrop);
    font-family: "Montserrat", sans-serif;
  }
  .canvas { position: relative; width: 1200px; height: 900px; }
  .card {
    position: absolute; left: 260px;
    width: 680px; height: 388px;
    border-radius: 26px;
    overflow: hidden;
    box-shadow: 0 6px 20px rgba(0,0,0,0.12);
  }
  .card--front { top: 36px; background: var(--paper); }
  .card--back { top: 476px; background: var(--navy); }

  .front__firm {
    position: absolute; left: 48px; top: 84px;
    font-weight: 300; font-size: 36px; letter-spacing: 3px;
    color: var(--navy); white-space: nowrap;
  }
  .front__mark {
    position: absolute; right: 40px; top: 72px;
    width: 170px; height: 270px;
    border-radius: 14px;
    background: linear-gradient(180deg, var(--navy-soft), var(--navy));
  }
  .front__accent {
    position: absolute; left: 0; top: 258px;
    width: 9px; height: 36px; background: var(--navy);
  }
  .front__name {
    position: absolute; left: 48px; top: 250px;
    font-weight: 700; font-size: 27px; color: var(--navy);
  }
  .front__title {
    position: absolute; left: 52px; top: 285px;
    font-weight: 400; font-size: 14px; color: var(--navy);
  }
  .contact {
    position: absolute; left: 52px; top: 316px;
    list-style: none;
  }
  .contact__item {
    display: flex; align-items: center; gap: 10px;
    font-size: 13px; line-height: 19px; color: var(--ink);
  }
  .contact__icon { width: 11px; height: 11px; fill: var(--navy); flex: none; }

  .back__logo {
    position: absolute; inset: 0;
    display: flex; align-items: center; justify-content: center; gap: 18px;
  }
  .back__square { width: 30px; height: 30px; background: var(--paper); }
  .back__firm {
    font-weight: 300; font-size: 46px; letter-spacing: 4px;
    color: var(--paper); white-space: nowrap;
  }
</style>
</head>
<body>
<main class="canvas">
  <section class="card card--front" aria-label="Business card front">
    <h1 class="front__firm">OAK PARTNERS</h1>
    <div class="front__mark" role="img" aria-label="Firm silhouette mark of two standing figures"></div>
    <span class="front__accent"></span>
    <p class="front__name">Dorian Pemberton</p>
    <p class="front__title">Attorney at Law</p>
    <ul class="contact">
      <li class="contact__item">
        <svg class="contact__icon" viewBox="0 0 12 12" aria-hidden="true"><path d="M2.5 1 L4.5 1 L5.2 3.5 L4 4.6 Q5 6.8 7.4 8 L8.5 6.8 L11 7.5 L11 9.5 Q10.5 11 9 11 Q1 10 1 3 Q1 1.5 2.5 1 Z"/></svg>
        <span>800-555-0147</span>
      </li>
      <li class="contact__item">
        <svg class="contact__icon" viewBox="0 0 12 12" aria-hidden="true"><path d="M0.5 2.5 H11.5 V10 H0.5 Z M1 3 L6 7 L11 3" stroke="#fff" stroke-width="0.8"/></svg>
        <span>dorian@oakpartners.example</span>
      </li>
      <li class="contact__item">
        <svg class="contact__icon" viewBox="0 0 12 12" aria-hidden="true"><circle cx="6" cy="6" r="5.5"/><path d="M0.5 6 H11.5 M6 0.5 Q3 6 6 11.5 M6 0.5 Q9 6 6 11.5" stroke="#fff" stroke-width="0.7" fill="none"/></svg>
        <span>www.oakpartners.example</span>
      </li>
    </ul>
  </section>

  <section class="card card--back" aria-label="Business card back">
    <div class="back__logo">
      <span class="back__square"></span>
      <span class="back__firm">OAK PARTNERS</span>
    </div>
  </section>
</main>
</body>
</html>
```